Website for Swedish wellness company "Heartmeadow"

We need a website for our Swedish wellness company. The name is "Heartmeadow" . The company is all about sustainablility for our body, soul and planet. We work with coaching, yoga, massage, healthy food, retreats(sports, excercise, sufing), healing and inspirational talks. We are convinced that personal sustainability and a strong spiritual connection to yourself will lead to planetary sustainability. Our customers are both companies and consumers from all over the world. The final design should be clean/simple and you should get a feeling of community, happiness, warmth, connection,, joy, spirituality but still a professional touch.Just got a logo from Pixel Harbor and are very happy with it;-)
Updates

Sorry I was too enthusiastic posting this project. Of course I will give you some text as well för the different pages! I will see to that it is finished by friday so if you want to wait with your submissions please do! Best regards Maria

Target Market(s)

Businesses and consumers

Industry/Entity Type

Health And Wellness

Number of Pages Required

5+ page

Font styles to use
Sans Serif

Colors
33a6d7
00a990
b7a5cd

Requirements
Must have
• Idea about pages:
• I am not sure how many pages I get for the price, but 5 would be nice to start with.
• Not sure what write ups is;-)
• But title of the pages could be:
• Landing page
• About us
• Services
• Retreats
• Contact us
Nice to have
• A clean and professional website but with some heart and soul in it. Because we Would love colours that harmonize with our logo, but other ideas are welcome!

```html
<!DOCTYPE html>
<html lang="en">
<head>
<meta charset="utf-8">
<title>Heartmeadow — Wellness for body, soul and planet</title>
<link rel="stylesheet" href="https://fonts.googleapis.com/css2?family=Montserrat:wght@400;500;600;700&family=Tinos:wght@400;700&family=Dancing+Script:wght@600;700&display=swap">
<style>
:root{
  --green:#00a990;
  --blue:#33a6d7;
  --lilac:#b7a5cd;
  --ink:#111;
  --text:#333;
  --muted:#666;
  --soft:#f2f2f2;
  --white:#fff;
  --footer:#1c1c1c;
}
*{margin:0;padding:0;box-sizing:border-box}
html,body{width:1200px;height:3593px;overflow:hidden}
body{position:relative;font-family:"Montserrat",Arial,sans-serif;color:var(--text);background:var(--white)}
.abs{position:absolute}
.serif{font-family:"Tinos","Times New Roman",serif}
.script{font-family:"Dancing Script",cursive;color:var(--green);font-weight:700}
.btn{position:absolute;background:var(--green);color:var(--white);border-radius:24px;font-size:13px;font-weight:500;display:flex;align-items:center;justify-content:center}
.photo{position:absolute}

/* hero */
.hero{position:absolute;left:0;top:0;width:1200px;height:611px;overflow:hidden;
  background:linear-gradient(180deg,#3f8fc8 0%,#7fb6de 45%,#cfe1ec 72%,#2d6f93 80%,#1f5a7c 100%)}
.hero-figure{left:560px;top:0;width:520px;height:611px;background:radial-gradient(ellipse at 55% 45%,#c9a48d 0%,#8f7b73 35%,rgba(90,110,130,0) 70%)}
.topbar{position:absolute;left:0;top:0;width:1200px;height:96px;background:rgba(30,80,120,.55)}
.brand{position:absolute;left:178px;top:18px;display:flex;flex-direction:column;align-items:center;color:var(--white)}
.brand .dot{width:40px;height:40px;border:2px solid var(--white);border-radius:50%}
.brand span{font-family:"Tinos",serif;font-size:18px;letter-spacing:1px;margin-top:4px}
.nav a{position:absolute;top:35px;height:34px;display:flex;align-items:center;justify-content:center;color:var(--white);font-size:13px;text-decoration:none}
.nav .active{background:var(--green);border-radius:18px}
.search{left:1011px;top:27px;width:40px;height:40px;border:1.5px solid var(--white);border-radius:50%}
.hero h1{left:158px;top:190px;font-size:76px;font-weight:400;color:var(--white)}
.hero p{left:158px;top:286px;width:320px;font-size:13px;line-height:24px;color:var(--white)}
.arrow{position:absolute;width:38px;height:38px;background:var(--white);display:flex;align-items:center;justify-content:center}

/* about */
.about-photo{left:162px;top:658px;width:312px;height:312px;border-radius:50%;background:radial-gradient(circle at 50% 40%,#d6c7b0,#7fa860 55%,#5d8a3f)}
.kicker{font-size:21px}
.h2{font-family:"Tinos","Times New Roman",serif;font-weight:700;color:var(--ink);font-size:31px}
.about p{left:522px;top:830px;width:525px;font-size:13px;line-height:27px;color:var(--text)}

/* services */
.services{left:0;top:1095px;width:1200px;height:522px;background:var(--soft)}
.sq{position:absolute;width:32px;height:32px;background:var(--white);display:flex;align-items:center;justify-content:center}
.card{position:absolute;top:1257px;width:211px;height:288px}
.card-label{position:absolute;background:var(--white);display:flex;flex-direction:column;align-items:center;justify-content:center;font-size:15px;font-weight:600;color:var(--ink)}
.card-label small{font-size:10px;font-weight:400;line-height:17px;text-align:center;color:var(--text);margin:8px 10px}

/* banner */
.banner{left:0;top:1617px;width:1200px;height:258px;background:linear-gradient(90deg,#3e3833 0%,#5e544c 45%,#8c6e58 75%,#4a3f37 100%)}
.banner h3{position:absolute;left:0;width:1200px;top:1664px;text-align:center;font-size:33px;font-weight:500;color:var(--white);letter-spacing:.5px}
.banner-text{left:300px;top:1725px;width:600px;text-align:center;font-size:13px;line-height:27px;color:var(--white)}

/* testimonials */
.stories{left:0;top:1875px;width:1200px;height:609px;background:var(--soft)}
.t-card{position:absolute;top:2096px;height:282px;background:var(--white);border-bottom:5px solid var(--green);box-shadow:0 4px 10px rgba(0,0,0,.12);overflow:hidden}
.avatar{position:absolute;width:106px;height:106px;border-radius:50%;border:4px solid var(--white);background:linear-gradient(160deg,#d9c2ae,#9b7d68)}
.t-name{position:absolute;font-size:20px;font-weight:600;color:var(--ink)}
.t-role{position:absolute;font-size:13px;color:var(--muted)}
.t-quote{position:absolute;font-size:12px;line-height:24px;color:var(--text)}
.t-mark{position:absolute;font-family:"Tinos",serif;font-size:150px;color:#e6e6e6;line-height:1}

/* news */
.post-photo{position:absolute;top:2630px;height:273px}
.post-meta{position:absolute;top:2928px;font-size:12px;color:var(--text);text-align:center}
.post-title{position:absolute;top:2962px;font-size:16px;line-height:25px;font-weight:700;color:var(--ink);text-align:center}

/* footer */
.footer{left:0;top:3137px;width:1200px;height:427px;background:var(--footer)}
.newsletter{left:141px;top:3099px;width:915px;height:108px;background:var(--green);border-radius:22px}
.newsletter h4{position:absolute;left:51px;top:28px;font-size:25px;line-height:40px;color:var(--white);font-weight:700}
.input{position:absolute;left:285px;top:31px;width:245px;height:48px;background:var(--white);border-radius:24px;font-size:12px;color:#aaa;display:flex;align-items:center;padding-left:30px}
.subscribe{position:absolute;left:542px;top:31px;width:115px;height:48px;background:var(--blue);border:2px solid var(--white);border-radius:24px;color:var(--white);font-size:14px;font-weight:600;display:flex;align-items:center;justify-content:center}
.social{position:absolute;top:3131px;width:42px;height:42px;border-radius:50%;background:var(--white)}
.f-brand{left:180px;top:3269px;display:flex;align-items:center;gap:14px;color:var(--white)}
.f-brand .dot{width:66px;height:66px;border:3px solid var(--green);border-radius:50%}
.f-brand span{font-family:"Tinos",serif;font-size:27px;letter-spacing:1px}
.f-about{left:178px;top:3378px;width:340px;font-size:12px;line-height:27px;color:var(--white)}
.f-head{position:absolute;top:3250px;font-size:21px;font-weight:700;color:var(--white)}
.f-links{left:587px;top:3302px;list-style:none;font-size:12px;line-height:30.5px;color:var(--white)}
.contact-row{position:absolute;left:792px;display:flex;gap:14px;font-size:12px;color:var(--white);line-height:30px}
.contact-row b{font-weight:700}
.copyright{left:0;top:3564px;width:1200px;height:29px;background:var(--green);color:var(--white);font-size:12px;display:flex;align-items:center;justify-content:center}
</style>
</head>
<body>

<!-- Hero -->
<section class="hero">
  <div class="photo hero-figure" role="img" aria-label="Woman meditating cross-legged by the sea under a blue sky"></div>
  <div class="topbar"></div>
  <div class="brand"><div class="dot"></div><span>HEARTMEADOW</span></div>
  <nav class="nav">
    <a class="active" style="left:551px;width:84px">Home</a>
    <a style="left:645px;width:70px">About us</a>
    <a style="left:735px;width:70px">Services</a>
    <a style="left:820px;width:70px">Retreats</a>
    <a style="left:910px;width:80px">Contact us</a>
    <div class="abs search">
      <svg width="37" height="37" viewBox="0 0 37 37"><circle cx="17" cy="17" r="6" fill="none" stroke="#fff" stroke-width="1.8"/><line x1="21.5" y1="21.5" x2="26" y2="26" stroke="#fff" stroke-width="1.8"/></svg>
    </div>
  </nav>
  <h1 class="abs serif">Heartmeadow</h1>
  <p class="abs">Lorem Ipsum is simply dummy text of the printing and typesetting industry. Lorem Ipsum has been the industry's standard dummy text</p>
  <div class="btn" style="left:148px;top:383px;width:111px;height:34px">Read More</div>
  <div class="arrow" style="left:53px;top:287px"><svg width="14" height="14" viewBox="0 0 14 14"><path d="M9 2 4 7l5 5" fill="none" stroke="#222" stroke-width="2"/></svg></div>
  <div class="arrow" style="left:1114px;top:287px"><svg width="14" height="14" viewBox="0 0 14 14"><path d="M5 2l5 5-5 5" fill="none" stroke="#222" stroke-width="2"/></svg></div>
</section>

<!-- About -->
<section class="about">
  <div class="photo about-photo" role="img" aria-label="Couple jogging together on a sunny park path"></div>
  <div class="abs script kicker" style="left:522px;top:730px">Some Story Behind Us</div>
  <h2 class="abs h2" style="left:522px;top:770px">We Have 20 Years of Ecperience</h2>
  <p class="abs">Lorem Ipsum is simply dummy text of the printing and typesetting industry. Lorem Ipsum has been the industry's standard dummy text ever since the 1500s, when an unknown printer took a galley of type and scrambled it to make a type specimen book. It has survived not only five centuries, but also the leap into electronic typesetting, remaining essentially unchanged.</p>
  <div class="btn" style="left:522px;top:975px;width:108px;height:34px">Read More</div>
</section>

<!-- Services -->
<section class="abs services"></section>
<div class="abs script" style="left:0;width:1200px;top:1148px;text-align:center;font-size:17px">What We Do</div>
<h2 class="abs h2" style="left:0;width:1200px;top:1180px;text-align:center">Our Services</h2>
<div class="sq" style="left:959px;top:1194px"><svg width="12" height="12" viewBox="0 0 12 12"><path d="M8 1 3 6l5 5" fill="#222"/></svg></div>
<div class="sq" style="left:1000px;top:1194px"><svg width="12" height="12" viewBox="0 0 12 12"><path d="M4 1l5 5-5 5" fill="#222"/></svg></div>

<div class="card" style="left:141px">
  <div class="photo" style="inset:0;background:linear-gradient(160deg,#e8d8cc,#b99b86 60%,#7f6a5e)" role="img" aria-label="Hands joined in a yoga pose"></div>
  <div class="card-label" style="left:17px;top:163px;width:177px;height:96px">
    <svg width="30" height="30" viewBox="0 0 30 30" fill="none" stroke="#00a990" stroke-width="1.8"><circle cx="15" cy="6" r="3"/><path d="M15 10v8M6 14l9 4 9-4M8 26l7-8 7 8"/></svg>
    <span style="margin-top:8px">Yoga</span>
  </div>
</div>
<div class="card" style="left:376px">
  <div class="photo" style="inset:0;background:linear-gradient(160deg,#c9a184,#8c6a55)" role="img" aria-label="Massage treatment in a spa"></div>
  <div class="card-label" style="left:17px;top:24px;width:177px;height:240px">
    <svg width="30" height="30" viewBox="0 0 30 30" fill="none" stroke="#00a990" stroke-width="1.8"><circle cx="15" cy="7" r="3"/><path d="M4 20h22M6 25h18M8 20c0-5 3-8 7-8s7 3 7 8"/></svg>
    <span style="margin-top:8px">Massage</span>
    <small>Lorem Ipsum is simply dummy text of the printing and typesetting</small>
    <div class="btn" style="position:static;width:86px;height:24px;font-size:10px">Read More</div>
  </div>
</div>
<div class="card" style="left:611px">
  <div class="photo" style="inset:0;background:linear-gradient(160deg,#f4f1ec,#d8c9b8 60%,#b5a48f)" role="img" aria-label="Smiling woman eating fresh salad"></div>
  <div class="card-label" style="left:17px;top:163px;width:177px;height:96px">
    <svg width="30" height="30" viewBox="0 0 30 30" fill="none" stroke="#00a990" stroke-width="1.8"><rect x="5" y="12" width="20" height="13" rx="2"/><path d="M9 12V7h12v5M9 18h12"/></svg>
    <span style="margin-top:8px">Healthy Food</span>
  </div>
</div>
<div class="card" style="left:845px">
  <div class="photo" style="inset:0;background:linear-gradient(160deg,#bcc6cd,#8696a1 60%,#5e6d77)" role="img" aria-label="Woman jumping mid-run against a grey wall"></div>
  <div class="card-label" style="left:17px;top:163px;width:177px;height:96px">
    <svg width="30" height="30" viewBox="0 0 30 30" fill="none" stroke="#00a990" stroke-width="1.8"><path d="M4 20c4 0 7-2 9-7l4 3c2 2 5 3 9 4v4H4z"/></svg>
    <span style="margin-top:8px">Sports</span>
  </div>
</div>

<!-- Banner -->
<section class="abs banner" role="img" aria-label="Woman in a sunlit meadow at dusk"></section>
<h3>A Natural way of improving your health.</h3>
<p class="abs banner-text">Lorem Ipsum is simply dummy text of the printing and typesetting industry. Lorem Ipsum has been the industry's standard dummy text ever since the 1500s</p>
<div class="btn" style="left:544px;top:1803px;width:110px;height:34px">Read More</div>

<!-- Testimonials -->
<section class="abs stories"></section>
<div class="abs script" style="left:163px;top:1930px;font-size:17px">Testimonials</div>
<h2 class="abs h2" style="left:163px;top:1962px">Successful Stories</h2>

<div class="t-card" style="left:141px;width:292px">
  <div class="t-mark" style="left:200px;top:190px">“</div>
</div>
<div class="avatar" style="left:158px;top:2058px" role="img" aria-label="Client portrait"></div>
<div class="t-name" style="left:287px;top:2118px">Ada Linwood</div>
<div class="t-role" style="left:287px;top:2150px">Client</div>
<p class="t-quote" style="left:167px;top:2210px;width:250px">"Sed ut perspiciatis unde omnis iste natus error sit voluptatem accusantium doloremque laudantium, totam rem aperiam, eaque ipsa quae ab illo</p>

<div class="t-card" style="left:455px;width:287px">
  <div class="t-mark" style="left:195px;top:190px">“</div>
</div>
<div class="avatar" style="left:470px;top:2058px" role="img" aria-label="Client portrait"></div>
<div class="t-name" style="left:602px;top:2118px">Tom Ellery</div>
<div class="t-role" style="left:602px;top:2150px">Client</div>
<p class="t-quote" style="left:481px;top:2210px;width:250px">"Sed ut perspiciatis unde omnis iste natus error sit voluptatem accusantium doloremque laudantium, totam rem aperiam, eaque ipsa quae ab illo</p>

<div class="t-card" style="left:766px;width:290px">
  <div class="t-mark" style="left:198px;top:190px">“</div>
</div>
<div class="avatar" style="left:783px;top:2058px" role="img" aria-label="Client portrait"></div>
<div class="t-name" style="left:912px;top:2118px">Noor</div>
<div class="t-role" style="left:912px;top:2150px">Client</div>
<p class="t-quote" style="left:792px;top:2210px;width:250px">"Sed ut perspiciatis unde omnis iste natus error sit voluptatem accusantium doloremque laudantium, totam rem aperiam, eaque ipsa quae ab illo</p>

<div class="abs" style="left:545px;top:2420px;width:30px;height:3px;background:var(--green)"></div>
<div class="abs" style="left:580px;top:2420px;width:30px;height:3px;background:#cfcfcf"></div>

<!-- News -->
<div class="abs script" style="left:0;width:1200px;top:2524px;text-align:center;font-size:17px">Our Blog</div>
<h2 class="abs h2" style="left:0;width:1200px;top:2558px;text-align:center">News &amp; Articles</h2>

<div class="post-photo" style="left:141px;width:292px;background:linear-gradient(160deg,#d8d2cc,#a79e96 60%,#7d776f)" role="img" aria-label="Person seated cross-legged in meditation"></div>
<div class="post-meta" style="left:141px;width:292px">April 30, 2019 &nbsp;|&nbsp; 10 Comments</div>
<div class="post-title" style="left:141px;width:292px">Lorem Ipsum is simply dummy<br>text of the printing</div>

<div class="post-photo" style="left:455px;width:290px;background:linear-gradient(170deg,#6b7f45,#b59b8a 55%,#d9b8b4)" role="img" aria-label="Pink running shoes on a log"></div>
<div class="post-meta" style="left:455px;width:290px">April 30, 2019 &nbsp;|&nbsp; 10 Comments</div>
<div class="post-title" style="left:455px;width:290px">Lorem Ipsum is simply dummy<br>text of the printing</div>

<div class="post-photo" style="left:769px;width:287px;background:linear-gradient(160deg,#f3f1ee,#ddd6cd 60%,#b9a99a)" role="img" aria-label="Woman holding a standing yoga pose"></div>
<div class="post-meta" style="left:769px;width:287px">April 30, 2019 &nbsp;|&nbsp; 10 Comments</div>
<div class="post-title" style="left:769px;width:287px">Lorem Ipsum is simply dummy<br>text of the printing</div>

<!-- Footer -->
<footer class="abs footer"></footer>
<div class="abs newsletter">
  <h4 class="serif">Subscribe<br>Our Newsletter</h4>
  <div class="input">Your Email Address</div>
  <div class="subscribe">Subscribe</div>
</div>
<div class="social" style="left:846px" role="img" aria-label="Social profile"></div>
<div class="social" style="left:899px" role="img" aria-label="Social profile"></div>
<div class="social" style="left:951px" role="img" aria-label="Social profile"></div>

<div class="abs f-brand"><div class="dot"></div><span>HEARTMEADOW</span></div>
<p class="abs f-about">Pellentesque congue non augue vitae pellentesque. Morbi sollicitudin eleifend rhoncus. Mauris vel nisi a magna viverra sollicitudin semper a diam.</p>

<div class="f-head" style="left:563px">Quick Links</div>
<ul class="abs f-links">
  <li>Home</li><li>About Us</li><li>Services</li><li>Retreats</li><li>Contact Us</li>
</ul>

<div class="f-head" style="left:786px">Contact Us</div>
<div class="contact-row" style="top:3302px">
  <svg width="22" height="22" viewBox="0 0 24 24" style="margin-top:4px"><path d="M6.6 10.8a15 15 0 0 0 6.6 6.6l2.2-2.2c.3-.3.7-.4 1-.2 1.1.4 2.3.6 3.6.6.6 0 1 .4 1 1V20c0 .6-.4 1-1 1A17 17 0 0 1 3 4c0-.6.4-1 1-1h3.5c.6 0 1 .4 1 1 0 1.3.2 2.5.6 3.6.1.3 0 .7-.2 1z" fill="#fff"/></svg>
  <span><b>Call Us:</b> 555-010-2040</span>
</div>
<div class="contact-row" style="top:3364px">
  <svg width="22" height="22" viewBox="0 0 24 24" style="margin-top:4px"><rect x="2" y="5" width="20" height="14" fill="none" stroke="#fff" stroke-width="2"/><path d="M2 5l10 8 10-8" fill="none" stroke="#fff" stroke-width="2"/></svg>
  <span><b>Email Us:</b> hello@heartmeadow.se</span>
</div>
<div class="contact-row" style="top:3424px">
  <svg width="22" height="22" viewBox="0 0 24 24" style="margin-top:4px"><path d="M12 2a7 7 0 0 0-7 7c0 5 7 13 7 13s7-8 7-13a7 7 0 0 0-7-7zm0 9.5A2.5 2.5 0 1 1 12 6.5a2.5 2.5 0 0 1 0 5z" fill="#fff"/></svg>
  <span><b>Address:</b> 12 Ängsvägen,<br>Uppsala</span>
</div>

<div class="abs copyright">© Copyright by Heartmeadow 2019</div>

</body>
</html>
```